Orvane Group Business Card

Building Management company based in Sydney, Australia. We provide onsite management for commercial and residential buildings.
I would like a sophisticated minimalist design that indicates that we provide a high-end service. I would like a silver or metal look background or something similar.
The business card should have:
Name
Title
email
Office Phone
Mobile
Address
Website
The services that we provide should be prominent:
Building Management - Concierge - Caretaking - Cleaning

```html
<!DOCTYPE html>
<html lang="en">
<head>
<meta charset="utf-8">
<title>Orvane Group – Business Card</title>
<link rel="stylesheet" href="https://fonts.googleapis.com/css2?family=Open+Sans:wght@400;600;700&display=swap">
<style>
  :root {
    --ink: #030303;
    --ink-sheen: #1e1f21;
    --brand-blue: #1a63a8;
    --brand-blue-light: #2b76bd;
    --paper: #ffffff;
    --silver-light: #f1f1f0;
    --silver-mid: #cfd0d1;
    --silver-dark: #b4b6b8;
  }
  * { box-sizing: border-box; margin: 0; padding: 0; }
  html, body {
    width: 1200px; height: 900px; overflow: hidden;
    font-family: "Open Sans", Arial, sans-serif;
  }
  body {
    background:
      repeating-linear-gradient(90deg, rgba(255,255,255,.10) 0 1px, rgba(0,0,0,.03) 1px 3px),
      linear-gradient(135deg, var(--silver-light) 0%, var(--silver-mid) 45%, var(--silver-light) 60%, var(--silver-dark) 100%);
  }
  .canvas {
    width: 1200px; height: 900px;
    display: flex; flex-direction: column;
    align-items: center; justify-content: center; gap: 50px;
  }
  .card {
    position: relative;
    width: 640px; height: 380px;
    overflow: hidden;
    box-shadow: 0 6px 18px rgba(0,0,0,.25);
  }
  .metal-dark { background: linear-gradient(160deg, var(--ink) 0%, var(--ink-sheen) 55%, var(--ink) 100%); }
  .metal-blue { background: linear-gradient(160deg, var(--brand-blue) 0%, var(--brand-blue-light) 55%, var(--brand-blue) 100%); }

  /* Back side */
  .card--back .band-top {
    position: absolute; left: 0; top: 0; width: 100%; height: 72px;
  }
  .card--back .band-bottom {
    position: absolute; left: 0; bottom: 0; width: 100%; height: 40px;
    display: flex; align-items: center; justify-content: center;
    color: var(--paper); font-size: 13px; font-weight: 600; letter-spacing: 1.5px;
    text-transform: uppercase;
  }
  .card--back .wordmark {
    position: absolute; left: 0; right: 0; top: 72px; bottom: 40px;
    display: flex; align-items: center; justify-content: center; gap: 14px;
    color: var(--paper);
    font-weight: 700; font-size: 38px; letter-spacing: 1px;
  }
  .mark-square {
    display: inline-block; width: 18px; height: 18px;
    background: var(--brand-blue);
  }

  /* Front side */
  .card--front .dark-top {
    position: absolute; left: 0; top: 0; width: 100%; height: 128px;
  }
  .card--front .dark-block {
    position: absolute; right: 0; top: 0; width: 310px; height: 232px;
  }
  .card--front .dark-foot {
    position: absolute; left: 0; bottom: 0; width: 100%; height: 34px;
  }
  .wordmark--front {
    position: absolute; right: 26px; top: 172px;
    color: var(--paper);
    font-weight: 700; font-size: 30px; letter-spacing: 1px; white-space: nowrap;
  }
  .person {
    position: absolute; left: 26px; top: 138px; color: var(--paper);
  }
  .person .name { font-weight: 700; font-size: 22px; line-height: 1.15; }
  .person .title { font-size: 13px; }
  .contacts {
    position: absolute; right: 26px; top: 244px;
    list-style: none; text-align: right; color: var(--paper);
    font-size: 16px; line-height: 20px;
  }
  .contacts li { display: flex; justify-content: flex-end; align-items: center; gap: 10px; white-space: nowrap; }
  .contacts svg { width: 13px; height: 13px; fill: var(--paper); flex: none; }
</style>
</head>
<body>
<main class="canvas">

  <section class="card card--back metal-dark" aria-label="Card back">
    <div class="band-top metal-blue"></div>
    <div class="wordmark"><span class="mark-square" aria-hidden="true"></span>ORVANE GROUP</div>
    <div class="band-bottom metal-blue">Building Management · Concierge · Caretaking · Cleaning</div>
  </section>

  <section class="card card--front metal-blue" aria-label="Card front">
    <div class="dark-top metal-dark"></div>
    <div class="dark-block metal-dark"></div>
    <div class="dark-foot metal-dark"></div>

    <div class="wordmark--front">ORVANE GROUP</div>

    <div class="person">
      <p class="name">Declan Reyes</p>
      <p class="title">Managing Director</p>
    </div>

    <ul class="contacts">
      <li>123.456.7890
        <svg viewBox="0 0 16 16" aria-label="Office phone"><path d="M1 6c0-2 3-3 7-3s7 1 7 3v1h-3V5.5C11 5 9.5 5 8 5s-3 0-4 .5V7H1zm3 2h8l2 5H2z"/></svg></li>
      <li>123.456.7890
        <svg viewBox="0 0 16 16" aria-label="Mobile"><path d="M4 1h8v14H4zm1.5 2v8h5V3zm2 9.5v1h1v-1z"/></svg></li>
      <li>info@youremail.com
        <svg viewBox="0 0 16 16" aria-label="Email"><path d="M1 3h14v10H1zm1.5 1.5L8 9l5.5-4.5z"/></svg></li>
      <li>www.website.com
        <svg viewBox="0 0 16 16" aria-label="Website"><path d="M6 10l4-4 1 1-4 4zM3 9l2-2 1 1-2 2 2 2 2-2 1 1-2 2a1.5 1.5 0 0 1-2 0l-2-2a1.5 1.5 0 0 1 0-2zm4-5l2-2a1.5 1.5 0 0 1 2 0l2 2a1.5 1.5 0 0 1 0 2l-2 2-1-1 2-2-2-2-2 2z"/></svg></li>
      <li>1234, Address Goes Here, Country Name, 123456
        <svg viewBox="0 0 16 16" aria-label="Address"><path d="M8 1a5 5 0 0 1 5 5c0 4-5 9-5 9S3 10 3 6a5 5 0 0 1 5-5zm0 3a2 2 0 1 0 0 4 2 2 0 0 0 0-4z"/></svg></li>
    </ul>
  </section>

</main>
</body>
</html>
```